Haulage company, lets use ruby red white and some 3rd color for web design. and Garvel Pryce Transport logo

Target Market(s)

Transport industry

Industry/Entity Type

transport

Number of Pages Required

2 page

Requirements
Must have
• Logo

```html
<!DOCTYPE html>
<html lang="en">
<head>
<meta charset="utf-8">
<title>Garvel Pryce Transport</title>
<link rel="stylesheet" href="https://fonts.googleapis.com/css2?family=Montserrat:wght@400;500;600;700&family=Roboto:wght@400;500&display=swap">
<style>
:root{
  --ruby:#9b1b22;
  --ruby-dark:#7e141a;
  --ink:#2f2f2f;
  --text:#4a4a4a;
  --muted:#8a8a8a;
  --white:#ffffff;
  --footer:#333333;
  --line:#d9d9d9;
}
*{box-sizing:border-box;margin:0;padding:0}
html,body{width:1200px;height:3831px;overflow:hidden;background:var(--white)}
body{font-family:"Roboto",Arial,sans-serif;color:var(--text)}
.page{position:relative;width:1200px;height:3831px;overflow:hidden}
.abs{position:absolute}
.heading{font-family:"Montserrat",sans-serif;font-weight:600;color:var(--ink);letter-spacing:.5px}
.btn{position:absolute;display:flex;align-items:center;justify-content:center;background:var(--ruby);color:var(--white);font-family:"Montserrat",sans-serif;font-weight:700;font-size:14px;border-radius:5px;text-transform:uppercase}

/* header */
.site-header{position:absolute;top:0;left:0;width:1200px;height:85px;background:var(--white);z-index:5}
.brand{position:absolute;left:112px;top:18px;display:flex;align-items:center;gap:10px}
.brand-square{width:12px;height:12px;background:var(--ruby)}
.brand-name{font-family:"Montserrat",sans-serif;font-weight:700;font-size:23px;line-height:26px;color:var(--ink);letter-spacing:.6px}
.nav a{position:absolute;top:34px;font-family:"Montserrat",sans-serif;font-size:16px;color:#555;text-decoration:none}
.login{left:974px;top:21px;width:114px;height:44px;font-size:14px}

/* hero */
.hero{position:absolute;top:85px;left:0;width:1200px;height:695px;z-index:3;
  background:linear-gradient(180deg,#b9c4cf 0%,#cfd5d8 45%,#a9a59c 70%,#c9c6c0 100%);
  clip-path:polygon(0 0,100% 0,100% 614px,601px 673px,0 592px)}
.hero-photo{position:absolute;left:0;top:0;width:100%;height:100%;
  background:radial-gradient(ellipse 300px 360px at 390px 330px,#eeeeec 0%,#e1dfdc 45%,rgba(225,223,220,0) 75%),
             radial-gradient(ellipse 200px 120px at 380px 560px,#8d2630 0%,rgba(141,38,48,0) 80%)}
.hero-band{position:absolute;top:85px;left:0;width:1200px;height:720px;z-index:2}
.hero-card{position:absolute;left:644px;top:260px;width:444px;height:327px;z-index:4;
  background:rgba(155,27,34,.86);border:2px solid var(--white);padding:26px 40px 0 42px;color:var(--white)}
.hero-card h1{font-family:"Montserrat",sans-serif;font-weight:600;font-size:49px;line-height:58px}
.hero-card p{font-size:15px;line-height:26px;margin-top:14px}
.hero-btn{display:inline-flex;align-items:center;justify-content:center;margin-top:20px;width:137px;height:43px;border:2px solid var(--white);border-radius:6px;font-family:"Montserrat",sans-serif;font-weight:700;font-size:14px}
.dots{position:absolute;top:714px;left:566px;display:flex;gap:5px;z-index:4}
.dots span{width:12px;height:12px;border-radius:50%;background:var(--white)}
.dots span:first-child{background:transparent;border:2px solid var(--white)}

/* services */
.services{position:absolute;top:660px;left:0;width:1200px;height:654px;z-index:1;
  background:linear-gradient(180deg,#e9e6e6 0%,#efeded 40%,#e6e2df 75%,#dcd6d0 100%)}
.services-title{position:absolute;top:848px;left:0;width:1200px;text-align:center;font-size:35px;z-index:2}
.card{position:absolute;top:925px;width:316px;height:312px;background:var(--white);
  border-bottom-right-radius:44px;box-shadow:0 4px 14px rgba(0,0,0,.08);z-index:2;text-align:center}
.card-inner{position:absolute;inset:8px;border:1.5px solid var(--ruby);border-bottom-right-radius:38px}
.card svg{position:absolute;left:50%;top:30px;transform:translateX(-50%)}
.card h3{position:absolute;top:126px;left:0;width:100%;font-family:"Montserrat",sans-serif;font-weight:500;font-size:19px;color:var(--ink)}
.card p{position:absolute;top:164px;left:26px;right:26px;font-size:14px;line-height:22px;color:var(--muted)}
.card .btn{left:89px;top:245px;width:137px;height:43px}

/* about */
.about-title{left:112px;top:1450px;font-size:35px}
.about-text{left:112px;top:1518px;width:422px;font-size:15px;line-height:26px;color:var(--text)}
.about-btn{left:112px;top:1759px;width:137px;height:43px}
.about-frame{left:583px;top:1419px;width:488px;height:423px;border:1.5px solid var(--ruby)}
.about-photo{left:599px;top:1401px;width:489px;height:425px;
  background:linear-gradient(180deg,#3d6fc4 0%,#7aa0d6 45%,#9c8a78 62%,#4a4646 80%,#3b3a3a 100%)}

/* feature band */
.feature{left:0;top:1930px;width:1200px;height:598px;
  background:linear-gradient(90deg,#5b5d60 0%,#d9dadc 18%,#e8e8ea 35%,#9aa5b2 60%,#8d98a6 100%)}
.feature-panel{left:635px;top:2015px;width:565px;height:428px;background:var(--white);border-left:8px solid var(--ruby);padding:50px 105px 0 52px}
.feature-panel h2{font-size:35px;line-height:44px}
.feature-panel p{margin-top:22px;font-size:14px;line-height:25px;text-align:justify}
.feature-btn{left:696px;top:2345px;width:137px;height:43px}

/* gallery */
.gallery-title{left:0;top:2607px;width:1200px;text-align:center;font-size:35px}
.tile{position:absolute;border-bottom-right-radius:60px}
.g1{left:112px;top:2683px;width:479px;height:328px;background:linear-gradient(160deg,#1a1d24 0%,#3a3c44 45%,#8b7a78 70%,#2a2b30 100%)}
.g2{left:608px;top:2683px;width:480px;height:328px;background:linear-gradient(180deg,#9cb0c8 0%,#c7ccd6 50%,#6b6e7a 75%,#3e4048 100%)}
.g3{left:112px;top:3025px;width:319px;height:307px;background:linear-gradient(180deg,#7b8fb0 0%,#e6b27c 40%,#f2c48a 50%,#4a4b55 75%,#2c2d34 100%)}
.g4{left:442px;top:3025px;width:319px;height:307px;background:linear-gradient(135deg,#8d7c5a 0%,#e0b864 35%,#c09050 55%,#5a4030 80%,#2a2020 100%)}
.g5{left:770px;top:3025px;width:320px;height:307px;background:linear-gradient(180deg,#8aa0c0 0%,#c8c0c8 40%,#8a3040 60%,#4a4a52 80%,#2e2f36 100%)}

/* footer */
.site-footer{left:0;top:3419px;width:1200px;height:412px;background:var(--footer);color:var(--white)}
.footer-brand{left:112px;top:3540px;display:flex;align-items:center;gap:10px}
.footer-brand .brand-name{color:var(--white);font-size:25px;line-height:29px}
.social{left:112px;top:3636px;display:flex;gap:28px}
.social span{width:20px;height:20px;border:2px solid var(--white);border-radius:50%}
.footer-col h4{font-family:"Montserrat",sans-serif;font-weight:500;font-size:21px;color:var(--white);letter-spacing:.5px}
.footer-col ul{list-style:none;margin-top:42px}
.footer-col li{font-family:"Montserrat",sans-serif;font-size:15px;line-height:30px;color:var(--white)}
.footer-divider{width:1px;height:198px;background:var(--ruby);top:3502px}
.contact-item{left:836px;display:flex;align-items:flex-start;gap:14px;font-family:"Montserrat",sans-serif;font-size:16px;line-height:26px;color:var(--white)}
.contact-item svg{flex:none}
.footer-rule{left:112px;top:3749px;width:1000px;height:1px;background:#6a6a6a}
.copyright{left:0;top:3779px;width:1200px;text-align:center;font-family:"Montserrat",sans-serif;font-size:12px;color:var(--white)}
</style>
</head>
<body>
<div class="page">

  <header class="site-header">
    <div class="brand">
      <div class="brand-name">GARVEL PRYCE<br>TRANSPORT</div>
      <span class="brand-square"></span>
    </div>
    <nav class="nav">
      <a style="left:410px">Home</a>
      <a style="left:495px">About Us</a>
      <a style="left:602px">Services</a>
      <a style="left:702px">Testimonials</a>
      <a style="left:836px">Contact Us</a>
    </nav>
    <span class="btn login">Log In</span>
  </header>

  <section class="hero" role="img" aria-label="Photo of a white and ruby red tractor unit parked on a yard">
    <div class="hero-photo"></div>
  </section>
  <svg class="hero-band" width="1200" height="720" viewBox="0 0 1200 720" aria-hidden="true">
    <polygon points="0,592 601,673 1200,614 1200,634 601,690 0,606" fill="var(--ruby)"/>
  </svg>
  <div class="hero-card">
    <h1>Garvel Pryce Transport</h1>
    <p>Lorem ipsum dolor sit amet, consectetur adipiscing elit, sed do eiusmod tempor incididunt ut labore et dolore magna aliqua.</p>
    <span class="hero-btn">GET STARTED</span>
  </div>
  <div class="dots"><span></span><span></span><span></span><span></span></div>

  <section class="services" role="img" aria-label="Faded photo of a truck on a country road"></section>
  <h2 class="heading services-title">OUR SERVICES</h2>

  <article class="card" style="left:112px">
    <div class="card-inner"></div>
    <svg width="120" height="64" viewBox="0 0 120 64" fill="none" stroke="#1d1d1d" stroke-width="3">
      <rect x="4" y="6" width="72" height="42"/>
      <line x1="8" y1="38" x2="72" y2="38" stroke="var(--ruby)"/>
      <path d="M76 18h22l14 16v14H76z"/>
      <path d="M84 22h12l9 11H84z"/>
      <circle cx="20" cy="52" r="7" fill="#fff"/><circle cx="38" cy="52" r="7" fill="#fff"/><circle cx="98" cy="52" r="7" fill="#fff"/>
    </svg>
    <h3>LOREM IPSUM DOLOR</h3>
    <p>Sed ut perspiciatis unde omnis ist natus error sit voluptatem accusantium dolor- emque laudantium, totam</p>
    <span class="btn">Learn More</span>
  </article>

  <article class="card" style="left:442px">
    <div class="card-inner"></div>
    <svg width="90" height="84" viewBox="0 0 90 84" fill="none" stroke="#1d1d1d" stroke-width="3" style="top:18px">
      <path d="M14 20h52a12 12 0 0 1 0 24H22a12 12 0 0 0 0 24h50"/>
      <path d="M14 30h50a3 3 0 0 1 0 6H24a20 20 0 0 0 0 40h46"/>
      <rect x="30" y="36" width="28" height="22" rx="3" fill="#fff"/>
      <circle cx="14" cy="12" r="8" stroke="var(--ruby)" fill="#fff"/>
      <circle cx="74" cy="64" r="8" stroke="var(--ruby)" fill="#fff"/>
    </svg>
    <h3>LOREM IPSUM DOLOR</h3>
    <p>Sed ut perspiciatis unde omnis ist natus error sit voluptatem accusantium dolor- emque laudantium, totam</p>
    <span class="btn">Learn More</span>
  </article>

  <article class="card" style="left:772px">
    <div class="card-inner"></div>
    <svg width="80" height="74" viewBox="0 0 80 74" fill="none" stroke="#1d1d1d" stroke-width="2.5" style="top:26px">
      <path d="M14 20c-6-7-8-10-8-13a8 8 0 0 1 16 0c0 3-2 6-8 13z" stroke="var(--ruby)"/>
      <path d="M66 20c-6-7-8-10-8-13a8 8 0 0 1 16 0c0 3-2 6-8 13z" stroke="var(--ruby)"/>
      <path d="M18 24q22 8 44 0" stroke="var(--ruby)" stroke-dasharray="3 4"/>
      <rect x="20" y="40" width="34" height="22"/>
      <path d="M54 46h12l8 8v8H54z"/>
      <circle cx="30" cy="64" r="5" fill="#fff"/><circle cx="64" cy="64" r="5" fill="#fff"/>
      <path d="M4 44h12M8 52h10M4 60h12"/>
    </svg>
    <h3>LOREM IPSUM DOLOR</h3>
    <p>Sed ut perspiciatis unde omnis ist natus error sit voluptatem accusantium dolor- emque laudantium, totam</p>
    <span class="btn">Learn More</span>
  </article>

  <h2 class="abs heading about-title">ABOUT US</h2>
  <p class="abs about-text">Lorem ipsum dolor sit amet, consectetur adipiscing elit, sed do eiusmod tempor incididunt ut labore et dolore magna aliqua. Ut enim ad minim veniam, quis nostrud exercitation ullamco laboris nisi ut aliquip ex ea commodo consequat. Duis aute irure dolor in reprehenderit in voluptate velit esse cillum dolore eu fugiat nulla pariatur. Excepteur sint occaecat cupidatat non proident, sunt in culpa qui officia deserunt mollit anim id est laborum.</p>
  <span class="btn about-btn">Learn More</span>
  <div class="abs about-frame"></div>
  <div class="abs about-photo" role="img" aria-label="Photo of a cream and ruby red tractor unit at sunset"></div>

  <section class="abs feature" role="img" aria-label="Photo of a white and ruby red truck with a box trailer in a yard"></section>
  <div class="abs feature-panel">
    <h2 class="heading">GARVEL PRYCE<br>TRANSPORT</h2>
    <p>Lorem ipsum dolor sit amet, consectetur adipiscing elit, sed do eiusmod tempor incididunt ut labore et dolore magna aliqua. Ut enim ad minim veniam, quis nostrud exercitation ullamco laboris nisi ut aliquip ex ea commodo consequat. Duis aute irure dolor in reprehenderit in voluptate velit esse cillum dolore eu fugiat nulla pariatur.</p>
  </div>
  <span class="btn feature-btn">Learn More</span>

  <h2 class="abs heading gallery-title">OUR GALLERY</h2>
  <div class="tile g1" role="img" aria-label="Photo of two trucks parked at night"></div>
  <div class="tile g2" role="img" aria-label="Photo of a truck driving on a highway at dusk"></div>
  <div class="tile g3" role="img" aria-label="Photo of a truck on a road at sunset"></div>
  <div class="tile g4" role="img" aria-label="Photo of a trailer speeding past in golden light"></div>
  <div class="tile g5" role="img" aria-label="Photo of a red truck with a trailer on a highway"></div>

  <footer class="abs site-footer"></footer>
  <div class="abs footer-brand">
    <div class="brand-name">GARVEL PRYCE<br>TRANSPORT</div>
    <span class="brand-square"></span>
  </div>
  <div class="abs social"><span></span><span></span><span></span><span></span></div>

  <div class="abs footer-col" style="left:382px;top:3498px">
    <h4>QUICK LINKS</h4>
    <ul><li>Home</li><li>About Us</li><li>Services</li><li>Testimonials</li><li>Contact Us</li></ul>
  </div>
  <div class="abs footer-divider" style="left:568px"></div>
  <div class="abs footer-col" style="left:626px;top:3498px">
    <h4>HELP LINK</h4>
    <ul><li>Terms &amp; Conditions</li><li>Privacy Policy</li><li>About Us</li><li>Support</li></ul>
  </div>
  <div class="abs footer-divider" style="left:794px"></div>
  <div class="abs footer-col" style="left:840px;top:3496px"><h4>OUR LOCATION</h4></div>

  <div class="abs contact-item" style="top:3562px">
    <svg width="30" height="30" viewBox="0 0 30 30" fill="none" stroke="#fff" stroke-width="1.5"><circle cx="15" cy="15" r="14"/><path d="M15 22c-4-5-5-7-5-9a5 5 0 0 1 10 0c0 2-1 4-5 9z"/><circle cx="15" cy="13" r="1.8"/></svg>
    <span>Lorem ipsum dolor amet,<br>consectetur adipi</span>
  </div>
  <div class="abs contact-item" style="top:3638px">
    <svg width="30" height="30" viewBox="0 0 30 30" fill="none" stroke="#fff" stroke-width="1.5"><circle cx="15" cy="15" r="14"/><path d="M10 9l3-1 2 4-2 1.5a8 8 0 0 0 3.5 3.5L18 15l4 2-1 3c-6 0-11-5-11-11z"/></svg>
    <span>+1 (888) 888 8888</span>
  </div>
  <div class="abs contact-item" style="top:3696px">
    <svg width="30" height="30" viewBox="0 0 30 30" fill="none" stroke="#fff" stroke-width="1.5"><circle cx="15" cy="15" r="14"/><rect x="8" y="10" width="14" height="10" rx="1"/><path d="M8 11l7 5 7-5"/></svg>
    <span>info@garvelprycetransport.com</span>
  </div>

  <div class="abs footer-rule"></div>
  <p class="abs copyright">©Copyrights 2024 Garvel Pryce Transport &nbsp;| &nbsp; All Rights Reserved</p>

</div>
</body>
</html>
```